www.brightpathlingo.com -- International Language school needs a Wordpress Design

NOTE: This is for a complete WordPress website with coding (Design/develop)

We are a small, private English language school in business for 15 years. Our students come from around the world to study English at our centre in Toronto, Canada. Most of our students are in their 20's and come to study English with us for periods of 1-6 months before returning home to complete their post-secondary education or pursue their careers.

We are looking for a talented web designer to redevelop our sadly outdated website (www.brightpathlingo.com) to bring a fresh look with vastly increased functionality and web traffic.

Target Market(s)

-20s and 30s; mostly upper-middle class, educated
-from non-English speaking countries, but often have some English background
-looking to improve their English (mostly speaking) skills at our school like ours and experience living in a new country (like exchange students)

Industry/Entity Type

Education

Font styles to use
Sans Serif

Requirements
Must have
• - page listing our programs
- page with our fees and starting dates
- application form
- page showing why BRIGHTPATH (us)?
- page with accommodation options
* responsive design
Nice to have
• examples of other websites in our industry I like:

http://www.morvale-tutors.com/
http://www.dunfieldlanguages.com/en
http://en.plm.ca/
http://www.harrowgate-study.ac.uk/

```html
<!DOCTYPE html>
<html lang="en">
<head>
<meta charset="utf-8">
<title>Brightpath English School</title>
<link href="https://fonts.googleapis.com/css2?family=Open+Sans:wght@300;400;600;700&family=Arimo:wght@400;700&display=swap" rel="stylesheet">
<style>
:root{
  --orange:#ef8a06;
  --orange-dark:#d97400;
  --orange-light:#f6a623;
  --charcoal:#2e2e2e;
  --topbar:#3b3b3b;
  --green:#1f9068;
  --green-line:#7cc4a9;
  --paper:#ffffff;
  --footer:#efefef;
  --ink:#333333;
  --muted:#777777;
  --rule:#dddddd;
  --photo-warm:#b99a82;
  --photo-cool:#8f9aa5;
}
*{box-sizing:border-box;margin:0;padding:0}
html,body{width:1200px;height:2345px;overflow:hidden}
body{position:relative;background:var(--paper);font-family:"Arimo",Arial,sans-serif;color:var(--ink)}
.band{position:absolute;left:0;width:1200px}
ul{list-style:none}

/* top bar */
.topbar{top:0;height:38px;background:var(--topbar);color:#ddd;font-size:11px;display:flex;align-items:center;padding-left:70px}
.topbar .info{display:flex;gap:26px;align-items:center}
.topbar .info span{display:flex;align-items:center;gap:6px}
.topbar .links{position:absolute;left:796px;display:flex;gap:16px}
.topbar .social{position:absolute;left:1008px;display:flex;gap:6px}
.topbar .social i{width:22px;height:22px;border:1.5px solid var(--orange);border-radius:50%;display:block}

/* header */
.header{top:38px;height:96px;background:linear-gradient(var(--orange-light),var(--orange));display:flex;align-items:center}
.brand{position:absolute;left:70px;display:flex;align-items:center;gap:10px;font-family:"Open Sans",sans-serif;font-weight:700;font-size:34px;color:#222;text-transform:lowercase}
.brand i{width:26px;height:26px;border-radius:50%;background:#222;display:block}
.nav{position:absolute;left:497px;display:flex;gap:16px;font-family:"Open Sans",sans-serif;font-size:13px;color:#fff;text-transform:uppercase}
.nav a{color:#fff;text-decoration:none}
.nav .current{color:#222;border-bottom:1px solid #222;padding-bottom:4px}

/* hero */
.hero{top:134px;height:360px;display:flex}
.hero .photo{width:828px;height:100%;background:linear-gradient(180deg,#f4f4f4 0%,#d9c7b8 55%,#f8f8f8 100%)}
.hero .slogan{flex:1;background:linear-gradient(135deg,#e9a000,#dc8c00);display:flex;align-items:center;justify-content:center;text-align:center;color:#fff;font-family:"Open Sans",sans-serif;font-weight:300;font-size:24px;letter-spacing:2px;line-height:1.1}

/* program strip */
.programs{top:494px;height:158px;background:var(--charcoal);color:#fff}
.programs .item{position:absolute;top:8px;width:243px;height:101px;text-align:center;font-family:"Open Sans",sans-serif;padding-top:4px}
.programs .item h2{font-weight:300;font-size:33px;line-height:1.1}
.programs .item p{font-size:12px;font-weight:700;margin-top:10px;font-family:"Arimo",sans-serif}
.programs .item.active{background:var(--orange)}

/* intro */
.intro-title{font-family:"Open Sans",sans-serif;font-size:20px;color:#222;position:absolute;top:686px}
.tabs-box{position:absolute;left:67px;top:720px;width:683px;height:377px;border:1px solid var(--rule);border-radius:3px}
.tabs{display:flex;height:36px;border-bottom:1px solid var(--rule);font-size:13px}
.tabs li{padding:0 15px;line-height:36px;border-right:1px solid var(--rule);color:#444}
.tabs li.on{color:var(--orange)}
.tabs li:last-child{border-right:0}
.gallery-pair{position:absolute;left:18px;top:60px;display:flex}
.gallery-pair div{height:182px}
.tabs-box p{position:absolute;left:18px;top:248px;width:650px;font-size:12px;line-height:17px;color:#666}
.tabs-box p b{color:#444}
.contact{position:absolute;left:809px;top:686px;width:334px}
.contact h3{font-family:"Open Sans",sans-serif;font-weight:400;font-size:20px;color:#222}
.fields{margin-top:22px;border:1px solid var(--rule)}
.fields div{height:36px;border-bottom:1px solid var(--rule);font-size:12px;color:#777;padding:0 10px;display:flex;align-items:center;justify-content:space-between}
.fields div:last-child{border-bottom:0}
.message{margin-top:13px;height:135px;border:1px solid var(--rule);font-size:12px;color:#777;padding:10px}
.actions{margin-top:16px;display:flex;justify-content:space-between;align-items:center}
.btn{background:var(--orange);color:#fff;font-size:12px;padding:8px 10px;border-radius:3px}
.clear{color:var(--orange);font-size:12px}

/* student corner */
.corner{top:1137px;height:317px;background:var(--green);color:#fff;text-align:center}
.corner h2{font-family:"Open Sans",sans-serif;font-weight:300;font-size:40px;padding-top:32px}
.corner .cols{position:absolute;top:100px;left:33px;right:33px;display:flex}
.corner .col{flex:1;height:184px;border-right:1px solid var(--green-line);padding:0 30px}
.corner .col:last-child{border-right:0}
.corner .col svg{display:block;margin:0 auto}
.corner h4{font-family:"Open Sans",sans-serif;font-weight:400;font-size:19px;color:#222;margin:14px 0 8px}
.corner .col p{font-size:12px;line-height:19px}
.totop{position:absolute;right:7px;top:52px;width:30px;height:30px;border-radius:50%;background:#3fa57f}

/* testimonials */
.voices{top:1454px;height:531px;background:var(--charcoal);color:#fff;text-align:center}
.voices h2{font-family:"Open Sans",sans-serif;font-weight:400;font-size:27px;padding-top:38px}
.quote{position:absolute;left:33px;top:87px;width:1146px;height:159px;border:1px solid #aaa;border-radius:3px;padding:18px 30px;font-family:"Open Sans",sans-serif;font-weight:600;font-size:17px;line-height:23px}
.author{position:absolute;left:36px;top:104px;display:flex;align-items:center;gap:12px;font-size:12px;color:#555;font-weight:400}
.author i{width:42px;height:42px;border-radius:50%;background:#c9b294;border:2px solid #eee;display:block}
.tab{position:absolute;left:0;top:209px;width:12px;height:60px;background:var(--orange)}
.dots{position:absolute;left:0;right:0;top:253px;color:#999;font-size:14px}
.voices h3{position:absolute;left:0;right:0;top:275px;font-family:"Open Sans",sans-serif;font-weight:400;font-size:28px}
.strip{position:absolute;left:33px;top:322px;display:flex;gap:16px}
.strip div{width:242px;height:170px}
.next{position:absolute;left:1150px;top:385px;width:24px;height:44px;background:var(--orange);border-radius:3px}

/* footer */
.footer{top:1985px;height:295px;background:var(--footer)}
.footer .col{position:absolute;top:82px}
.footer h5{font-family:"Open Sans",sans-serif;font-weight:400;font-size:14px;color:#333;text-transform:uppercase;margin-bottom:16px}
.footer li{font-size:12px;line-height:17px;color:#777}
.post{display:flex;gap:14px}
.post i{width:52px;height:52px;border-radius:50%;border:1px solid #ddd;display:block}
.post b{font-weight:400;font-size:12px;color:#777;display:block;margin-top:4px}
.post small{font-size:10px;color:#555}
.thumbs{display:grid;grid-template-columns:repeat(4,52px);gap:3px}
.thumbs div{height:50px}

.base{top:2280px;height:65px;border-top:1px solid var(--rule);display:flex;align-items:center}
.base .brand{left:128px;font-size:30px}
.base .powered{position:absolute;left:331px;font-size:10px;color:#555}
.base .up{position:absolute;right:-8px;bottom:-10px;width:34px;height:34px;border-radius:50%;background:#f0c48a}
</style>
</head>
<body>

<div class="band topbar">
  <div class="info">
    <span><svg width="9" height="11" viewBox="0 0 9 11"><path d="M4.5 0a4 4 0 0 1 4 4c0 3-4 7-4 7s-4-4-4-7a4 4 0 0 1 4-4z" fill="#ddd"/><circle cx="4.5" cy="4" r="1.5" fill="#3b3b3b"/></svg>418 Larkin Avenue, Suite 12 Toronto, Ontario M5R 3K1 Canada</span>
    <span><svg width="8" height="11" viewBox="0 0 8 11"><rect x="1" y="0" width="6" height="11" rx="1" fill="#ddd"/></svg>+1-416-555-0182</span>
    <span><svg width="12" height="9" viewBox="0 0 12 9"><rect width="12" height="9" fill="#ddd"/><path d="M0 0l6 5 6-5" stroke="#3b3b3b" fill="none"/></svg>info@brightpathlingo.com</span>
    <span><svg width="11" height="11" viewBox="0 0 11 11"><circle cx="5.5" cy="5.5" r="4.5" stroke="#ddd" fill="none"/><path d="M5.5 3v3h2" stroke="#ddd" fill="none"/></svg>9am -4pm</span>
  </div>
  <div class="links"><span>News</span><span>Agent</span><span>Download</span></div>
  <div class="social"><i></i><i></i><i></i><i></i><i></i></div>
</div>

<div class="band header">
  <div class="brand"><i></i>brightpath</div>
  <nav class="nav">
    <a class="current">Home</a><a>Our School ▾</a><a>Programs ▾</a><a>Fees &amp; Dates ▾</a><a>Accommodation ▾</a><a>Students Corner ▾</a>
  </nav>
</div>

<div class="band hero">
  <div class="photo" role="img" aria-label="Group photo of five smiling young students"></div>
  <div class="slogan">make friends around<br>the world</div>
</div>

<div class="band programs">
  <div class="item active" style="left:67px"><h2>ENGLISH<br>COURSES</h2><p>find our our all programs</p></div>
  <div class="item" style="left:345px"><h2>Full-Time<br>Programs</h2><p>Intensive Focus</p></div>
  <div class="item" style="left:628px"><h2>Brightpath Junior<br>Programs</h2><p>Parent &amp; Child</p></div>
  <div class="item" style="left:902px"><h2>Special<br>Programs</h2><p>University Bridge</p></div>
</div>

<h2 class="intro-title" style="left:67px;font-weight:400">Learn English from expert. Join Brightpath today</h2>
<div class="tabs-box">
  <ul class="tabs"><li class="on">About us</li><li>Why Brightpath ?</li><li>Our Features</li><li>F A Q</li><li>Apply Online</li></ul>
  <div class="gallery-pair">
    <div role="img" aria-label="Students studying together around a classroom table" style="width:392px;background:linear-gradient(135deg,#a8735a,#6e6a70)"></div>
    <div role="img" aria-label="Two students smiling in the school lounge" style="width:276px;background:linear-gradient(135deg,#7d8288,#b49c8e)"></div>
  </div>
  <p><b>Lorem Ipsum</b> is simply dummy text of the printing and typesetting industry. Lorem Ipsum has been the industry's standard dummy text ever since the 1500s, when an unknown printer took a galley of type and scrambled it to make a type specimen book. It has survived not only five centuries, but also the leap into electronic typesetting, remaining essentially unchanged. It was popularised in the 1960s with the release of Letraset sheets containing Lorem Ipsum passages, and more recently with desktop publishing software like Aldus PageMaker including versions of Lorem Ipsum.</p>
</div>

<div class="contact">
  <h3>Get in touch with Brightpath</h3>
  <div class="fields">
    <div>Name *<span>◦</span></div>
    <div>E-mail *<span>✉</span></div>
    <div>Telephone<span>✆</span></div>
    <div>Country<span>⌖</span></div>
  </div>
  <div class="message">Message *</div>
  <div class="actions"><span class="btn">Send message</span><span class="clear">clear ⊗</span></div>
</div>

<div class="band corner">
  <h2>Student Corner</h2>
  <span class="totop"></span>
  <div class="cols">
    <div class="col">
      <svg width="54" height="44" viewBox="0 0 54 44"><path d="M4 16h10l16-12v36L14 28H4z" fill="var(--orange)"/><path d="M36 14q5 8 0 16M42 9q9 13 0 26" stroke="var(--orange)" stroke-width="4" fill="none"/></svg>
      <h4>News &amp; Events</h4><p>simply dummy text of the printing and typesetting industry. Lorem Ipsum has been the industry's standard dummy text ever since the 1500s,</p>
    </div>
    <div class="col">
      <svg width="54" height="44" viewBox="0 0 54 44"><path d="M12 2h34l-8 40H4z" fill="var(--orange)"/><path d="M17 12h22M15 20h22M13 28h22" stroke="var(--green)" stroke-width="2"/></svg>
      <h4>Lessons</h4><p>simply dummy text of the printing and typesetting industry. Lorem Ipsum has been the industry's standard dummy text ever since the 1500s,</p>
    </div>
    <div class="col">
      <svg width="54" height="44" viewBox="0 0 54 44"><rect x="4" y="6" width="46" height="34" rx="4" fill="var(--orange)"/><circle cx="27" cy="23" r="10" fill="var(--green)"/><circle cx="27" cy="23" r="6" fill="var(--orange)"/></svg>
      <h4>Photo Gallery</h4><p>simply dummy text of the printing and typesetting industry. Lorem Ipsum has been the industry's standard dummy text ever since the 1500s,</p>
    </div>
    <div class="col">
      <svg width="54" height="44" viewBox="0 0 54 44"><rect x="8" y="18" width="9" height="22" fill="var(--orange)"/><path d="M20 40V19l8-15q5 0 4 8l-2 6h14q4 1 3 5l-4 15q-1 2-4 2z" fill="var(--orange)"/></svg>
      <h4>Meet our students</h4><p>simply dummy text of the printing and typesetting industry. Lorem Ipsum has been the industry's standard dummy text ever since the 1500s,</p>
    </div>
  </div>
</div>

<div class="band voices">
  <h2>What our students says about Brightpath English School</h2>
  <div class="quote">Lorem Ipsum is simply dummy text of the printing and typesetting industry. Lorem Ipsum has been the industry's standard dummy text ever since the 1500s, when an unknown printer took a galley of type and scrambled it to make a type specimen book. It has survived not only five centuries, but also the leap into electronic typesetting, remaining essentially unchanged.
    <div class="author"><i></i>Maria Lopes – Brazil</div>
  </div>
  <span class="tab"></span>
  <div class="dots">. . .</div>
  <h3>Students Gallery</h3>
  <div class="strip">
    <div role="img" aria-label="Students skating on an outdoor ice rink" style="background:linear-gradient(#9aa3ad,#d8dde2)"></div>
    <div role="img" aria-label="Friends laughing at a dinner table" style="background:linear-gradient(135deg,#7a5a44,#c8b7a0)"></div>
    <div role="img" aria-label="Group of students at a holiday party" style="background:linear-gradient(135deg,#5b4f4a,#a28a78)"></div>
    <div role="img" aria-label="Students building a gingerbread house" style="background:linear-gradient(135deg,#6f6a66,#c4a98f)"></div>
    <div role="img" aria-label="Students celebrating together" style="background:linear-gradient(135deg,#6c5a52,#a8968a)"></div>
  </div>
  <span class="next"></span>
</div>

<div class="band footer">
  <div class="col" style="left:120px"><h5>Knowledgebase</h5>
    <ul><li>Tips &amp; Tricks</li><li>Downloads</li><li>Articles and Magazines</li><li>Learn from the beginning</li><li>Tips &amp; Tricks</li><li>Downloads</li><li>Articles and Magazines</li><li>Learn from the beginning</li></ul></div>
  <div class="col" style="left:370px"><h5>News &amp; Blogs</h5>
    <div class="post"><i></i><div><b>Hello world!</b><small>February 7, 2015</small></div></div></div>
  <div class="col" style="left:621px"><h5>Gallery</h5>
    <div class="thumbs" role="img" aria-label="Small gallery thumbnails of school life">
      <div style="background:#8a6a62"></div><div style="background:#6f7478"></div><div style="background:#5f7a55"></div><div style="background:#7a6a70"></div>
      <div style="background:#9aa3ad"></div><div style="background:#6a5e5a"></div>
    </div></div>
  <div class="col" style="left:869px"><h5>Help Desk</h5>
    <ul><li>Student Forum</li><li>Course Enquiry</li><li>Classes and Time</li><li>Fees details</li><li>Apply online</li></ul></div>
</div>

<div class="band base">
  <div class="brand"><i></i>brightpath</div>
  <span class="powered">Powered By : webloom</span>
  <span class="up"></span>
</div>

</body>
</html>
```